Oil and Gas Exploration and Production company needs a business card design

We need a business card design using our logo and colors in the logo. We want a mainstream design.

```html
<!DOCTYPE html>
<html lang="en">
<head>
<meta charset="utf-8">
<title>Soltara Oil &amp; Gas — Business Card</title>
<link rel="stylesheet" href="https://fonts.googleapis.com/css2?family=Barlow:wght@400;500;600&display=swap">
<style>
  :root {
    --gold: #c99a33;
    --gold-light: #f2e7cc;
    --gold-mid: #dcbd78;
    --ink: #161616;
    --paper: #ffffff;
    --stage: #e9e9ea;
    --text: #2a2a2a;
  }
  * { box-sizing: border-box; margin: 0; padding: 0; }
  html, body { width: 1200px; height: 1200px; overflow: hidden; }
  body {
    background: var(--stage);
    font-family: "Barlow", sans-serif;
    position: relative;
  }
  .card {
    position: absolute;
    left: 160px;
    width: 880px;
    height: 503px;
    overflow: hidden;
    box-shadow: 0 6px 18px rgba(0,0,0,0.12);
  }
  .card--front {
    top: 70px;
    background: radial-gradient(ellipse at 50% 45%, var(--gold-light) 0%, var(--gold-mid) 60%, var(--gold) 100%);
  }
  .card--back { top: 627px; background: var(--paper); }

  .brand {
    position: absolute;
    display: flex;
    align-items: center;
    gap: 14px;
    color: var(--ink);
    font-weight: 600;
    letter-spacing: 0.5px;
    white-space: nowrap;
    line-height: 1;
  }
  .brand__dot {
    border-radius: 50%;
    background: var(--ink);
    flex: none;
  }
  .card--front .brand {
    left: 50%; top: 50%;
    transform: translate(-50%, -50%);
    font-size: 58px;
  }
  .card--front .brand__dot { width: 46px; height: 46px; }
  .card--back .brand { left: 70px; top: 150px; font-size: 44px; }
  .card--back .brand__dot { width: 36px; height: 36px; }

  .holder {
    position: absolute;
    right: 80px; top: 70px;
    text-align: right;
  }
  .holder__name {
    color: var(--gold);
    font-size: 34px;
    font-weight: 400;
    letter-spacing: 0.5px;
    line-height: 1;
  }
  .holder__title { color: var(--text); font-size: 14px; margin-top: 4px; }
  .rule {
    position: absolute;
    height: 1px;
    background: var(--gold);
  }
  .rule--top { right: 60px; top: 140px; width: 360px; }
  .rule--left { left: 60px; top: 270px; width: 330px; }

  .address {
    position: absolute;
    right: 80px; top: 170px;
    text-align: right;
    font-size: 17px;
    color: var(--text);
    line-height: 1.35;
  }
  .address svg { vertical-align: -2px; margin-left: 6px; }

  .contacts {
    position: absolute;
    left: 70px; top: 285px;
    list-style: none;
    font-size: 20px;
    color: var(--text);
    line-height: 1.45;
  }
  .contacts li { display: flex; align-items: center; gap: 10px; }
  .contacts svg { flex: none; }

  .footer-band { position: absolute; left: 0; bottom: 0; }
  .website {
    position: absolute;
    right: 70px; bottom: 40px;
    color: var(--paper);
    font-size: 24px;
    font-weight: 500;
    letter-spacing: 3px;
  }
</style>
</head>
<body>

<section class="card card--front" aria-label="Card front">
  <div class="brand"><span class="brand__dot"></span>Soltara Oil &amp; Gas</div>
</section>

<section class="card card--back" aria-label="Card back">
  <div class="brand"><span class="brand__dot"></span>Soltara Oil &amp; Gas</div>

  <div class="holder">
    <p class="holder__name">JOHN DOE</p>
    <p class="holder__title">Director</p>
  </div>
  <div class="rule rule--top"></div>

  <p class="address">
    Dummy city<svg width="12" height="15" viewBox="0 0 12 15"><path d="M6 0a6 6 0 0 0-6 6c0 4.5 6 9 6 9s6-4.5 6-9a6 6 0 0 0-6-6zm0 8.5A2.5 2.5 0 1 1 6 3.5a2.5 2.5 0 0 1 0 5z" fill="var(--gold)"/></svg><br>
    Dummy Country Land
  </p>

  <div class="rule rule--left"></div>
  <ul class="contacts">
    <li><svg width="18" height="16" viewBox="0 0 18 16"><path d="M2 4c0-2 3-3 7-3s7 1 7 3v2h-4V4.5H6V6H2zM4 7h10l2 8H2z" fill="var(--gold)"/></svg>1-234-567890</li>
    <li><svg width="18" height="18" viewBox="0 0 18 18"><circle cx="9" cy="9" r="7.5" fill="none" stroke="var(--gold)" stroke-width="2"/><path d="M1.5 9h15M9 1.5c-3 3.5-3 11.5 0 15M9 1.5c3 3.5 3 11.5 0 15" fill="none" stroke="var(--gold)" stroke-width="1.5"/></svg>1-234-567890</li>
    <li><svg width="18" height="14" viewBox="0 0 18 14"><rect x="0" y="0" width="18" height="14" fill="var(--gold)"/><path d="M0 0l9 7 9-7" fill="none" stroke="var(--paper)" stroke-width="1.5"/></svg>john@soltaraoilgas.com</li>
  </ul>

  <svg class="footer-band" width="880" height="130" viewBox="0 0 880 130" aria-hidden="true">
    <polygon points="0,22 560,22 548,44 0,44" fill="var(--ink)"/>
    <polygon points="0,60 555,60 590,0 880,0 880,130 0,130" fill="var(--gold)"/>
  </svg>
  <p class="website">www.soltaraoilgas.com</p>
</section>

</body>
</html>
```